Sustainably Transforming Education

Company is education services based. early learning through adult and corporate. Focus is national government policy and program design and delivery alongside a research based and academically grounded set of approaches to planning, evaluation, and change management.I am looking for an innovative design position that aligns with the global agendas for innovation, creativity and collaboration at international and national policy levels (berulo is a name that reflects these qualities - colours need to reflect amythyst in some way). I also need a design that translates from a business card as 1 medium of interaction to a template that can work in word/powerpoint etc to support both stationery as well as a digital strategy across multiple channels (fb/twit/etc)There is no slogan/tag line for the company and their is no logo. I was looking to just leverage the name - have currently played around with various fonts (ending up with cuisine - all lowercase).

Industry/Entity Type

Adult

Contact Information for Business Card

name: berulo (all lowercase)Chairman: Andrew CrowMobile: +61 418 902 131Web: www.berulo.comemail: martin.pelly@berulo-example.com

Font styles to use
Script
Other font styles liked:
• cuisine

Colors
e34298
e667a6
33a6d7
aaaaaa

Requirements
Nice to have
• https://files.example-share.net/sh/qx7kw2hd91lzmnp/AAFr3tYbQeLp8VwZnKcDs2Hu?dl=0
• Link to the printwell templates used to begin this process....the one with the lines was about people intersecting (collaborating).....the organic shapes one more of a fluid feel of people coming together - the overall shape being largely spherical could represent a "global" feel.....anyway that is how I was thinking about these

```html
<!DOCTYPE html>
<html lang="en">
<head>
<meta charset="utf-8">
<title>berulo – Business Card</title>
<link rel="stylesheet" href="https://fonts.googleapis.com/css2?family=Kaushan+Script&display=swap">
<style>
  :root {
    --magenta: #e34298;
    --rose: #e667a6;
    --sky: #33a6d7;
    --rule-blue: #1b96d4;
    --ink: #1a1a1a;
    --white: #ffffff;
    --map-tint: rgba(255, 255, 255, 0.22);
    --script: "Kaushan Script", cursive;
  }
  html, body {
    margin: 0;
    padding: 0;
    width: 1200px;
    height: 740px;
    overflow: hidden;
    background: var(--magenta);
  }
  .card {
    position: relative;
    width: 1200px;
    height: 740px;
    overflow: hidden;
    font-family: var(--script);
  }
  .card__backdrop {
    position: absolute;
    inset: 0;
    width: 1200px;
    height: 740px;
  }
  .backdrop__base { fill: var(--magenta); }
  .backdrop__band { fill: var(--rose); }
  .backdrop__wave { fill: var(--sky); }
  .backdrop__corner { fill: var(--magenta); }

  .world-map {
    position: absolute;
    left: 356px;
    top: 176px;
    width: 592px;
    height: 352px;
    border-radius: 48% 52% 44% 56% / 50% 46% 54% 50%;
    background: radial-gradient(ellipse at 50% 45%, rgba(255,255,255,0.26), rgba(255,255,255,0.14) 70%, rgba(255,255,255,0) 100%);
  }

  .identity__name {
    position: absolute;
    left: 320px;
    top: 78px;
    margin: 0;
    font-size: 80px;
    font-weight: 400;
    line-height: 1;
    color: var(--white);
    white-space: nowrap;
  }
  .identity__role {
    position: absolute;
    left: 326px;
    top: 168px;
    margin: 0;
    font-size: 44px;
    font-weight: 400;
    line-height: 1;
    color: var(--ink);
  }
  .identity__rule {
    position: absolute;
    left: 326px;
    top: 227px;
    width: 760px;
    height: 3px;
    background: var(--rule-blue);
  }

  .contact {
    position: absolute;
    left: 620px;
    top: 322px;
    margin: 0;
    padding: 0;
    list-style: none;
  }
  .contact__item {
    display: flex;
    align-items: center;
    height: 46px;
    font-size: 25px;
    color: var(--white);
    white-space: nowrap;
  }
  .contact__icon {
    width: 30px;
    height: 30px;
    margin-right: 16px;
    flex: none;
  }
  .contact__icon * { fill: var(--magenta); }
  .contact__icon .icon-stroke { fill: none; stroke: var(--magenta); stroke-width: 1.6; }

  .brand {
    position: absolute;
    left: 76px;
    top: 548px;
    margin: 0;
    font-size: 96px;
    font-weight: 400;
    line-height: 1;
    color: var(--white);
  }
</style>
</head>
<body>
  <main class="card">
    <svg class="card__backdrop" viewBox="0 0 1000 617" preserveAspectRatio="none" aria-hidden="true">
      <rect class="backdrop__base" x="0" y="0" width="1000" height="617"/>
      <path class="backdrop__band" d="M370,0 L1000,0 L1000,540 C985,440 960,340 915,250 C860,130 680,40 370,0 Z"/>
      <path class="backdrop__corner" d="M520,0 L1000,0 L1000,330 C960,200 820,60 520,0 Z"/>
      <path class="backdrop__wave" d="M0,0 L370,0 C650,45 840,120 895,250 C945,360 970,440 1000,500 L1000,617 L585,617 C400,490 150,300 0,70 Z"/>
    </svg>

    <div class="world-map" role="img" aria-label="Faint world map silhouette behind the contact details"></div>

    <h1 class="identity__name">Martin Pelly</h1>
    <p class="identity__role">Chairman</p>
    <div class="identity__rule"></div>

    <ul class="contact">
      <li class="contact__item">
        <svg class="contact__icon" viewBox="0 0 24 24" aria-hidden="true">
          <path d="M4 9c0-3 3.5-5 8-5s8 2 8 5v1.5h-4V8.5c-1-.6-2.5-.9-4-.9s-3 .3-4 .9v2H4z"/>
          <path d="M7 11h10l2 8H5z"/>
        </svg>
        <span>+61 427 315 086</span>
      </li>
      <li class="contact__item">
        <svg class="contact__icon" viewBox="0 0 24 24" aria-hidden="true">
          <rect x="2" y="5" width="20" height="14"/>
          <path d="M2.8 5.8 12 13l9.2-7.2" fill="none" stroke="#ffffff" stroke-width="1.4"/>
          <path d="M2.8 18.2 9.5 11.5M21.2 18.2 14.5 11.5" fill="none" stroke="#ffffff" stroke-width="1.2"/>
        </svg>
        <span>martin.pelly@berulo-example.com</span>
      </li>
      <li class="contact__item">
        <svg class="contact__icon" viewBox="0 0 24 24" aria-hidden="true">
          <circle class="icon-stroke" cx="12" cy="12" r="9.5"/>
          <ellipse class="icon-stroke" cx="12" cy="12" rx="4.2" ry="9.5"/>
          <path class="icon-stroke" d="M12 2.5v19M2.5 12h19M4 7h16M4 17h16"/>
        </svg>
        <span>www.berulo-example.com</span>
      </li>
    </ul>

    <p class="brand">berulo</p>
  </main>
</body>
</html>
```